Distribution/Printing company needs a web site to inform prospective customers on what we do.

Distribution/Printing/Packaging company needs a web site to inform prospective customers on what we do. Please look at our direct to consumer web site (under development) for an idea of the product lines we sell: storedev.maplewickhaven.com
Logo files are attached as is a flyer that is under development which contains other information about the company (this is to be used for content- not to be posted as is). The web site should be focused on our business customer base and is not intended to be direct to consumer. Site should have a link to our consumer web site.
Site design should be mobile friendly, or mobile could be redirected to a mobile version. This web site will be strictly informational and will not be designed for any sales transactions.

Target Market(s)

Manufacturing and retail businesses, any other multi-site business that would benefit from centralized pricing and budget controls we can provide (banks, medical/dental offices, educational facilities, etc).

Industry/Entity Type

It Company

Coding

Coded - Design and coding required

Number of Pages Required

5+ page

Requirements
Must have
• 1) Top level menu: Products, about us, locations, contact us, news
• 2) page with news/promotions that is easily updated
• 3) "contact us" form (name, company, phone, email address) email link
• 4) link to www.store.maplewickhaven.com with information that lower pricing is available for businesses
• 5) SEO keywords
• 6) Link to powerpoint presentation file
Nice to have
• 1) our phone number should appear on every page near the top

```html
<!DOCTYPE html>
<html lang="en">
<head>
<meta charset="utf-8">
<title>Maplewick Haven Supply — Packaging, Printing, Distribution</title>
<link rel="stylesheet" href="https://fonts.googleapis.com/css2?family=Open+Sans:wght@400;600;700&display=swap">
<style>
:root{
  --ink:#1d1d1d;
  --text:#555;
  --muted:#9a9a9a;
  --link:#1b56a8;
  --band:#050505;
  --footer:#1f1f1f;
  --line:#e3e3e3;
  --white:#fff;
}
*{margin:0;padding:0;box-sizing:border-box}
html,body{width:837px;height:1200px;overflow:hidden;background:var(--white)}
body{position:relative;font-family:"Open Sans",Arial,sans-serif;color:var(--ink)}
.abs{position:absolute}

/* header */
.brand{left:69px;top:14px;width:150px}
.brand-mark{display:block;margin-left:28px}
.brand-name{font-size:10px;font-weight:700;letter-spacing:.2px;margin-top:2px;white-space:nowrap}
.brand-tag{font-size:6.8px;font-weight:600;margin-left:5px;white-space:nowrap}
.call{right:70px;top:16px;font-size:9px;color:#555;display:flex;align-items:center;gap:4px}
.call strong{font-size:13px;font-weight:400;color:var(--ink)}
.nav{top:53px;font-size:9.5px;color:#444}
.nav.active{color:var(--ink)}
.nav-underline{left:322px;top:69px;width:16px;height:2px;background:var(--ink)}

/* hero band */
.band{left:0;top:82px;width:837px;height:568px;background:var(--band)}
.slide{left:69px;top:106px;width:699px;height:317px;background:var(--white);padding:5px}
.slide-photo{width:100%;height:100%;background:
  radial-gradient(ellipse 40% 45% at 78% 75%,rgba(196,156,108,.95),rgba(196,156,108,0) 100%),
  radial-gradient(ellipse 30% 60% at 62% 40%,rgba(38,86,170,.9),rgba(38,86,170,0) 100%),
  linear-gradient(100deg,#a57d14 0%,#d9ad2c 30%,#c99c28 48%,#2e4f86 70%,#4d6a4a 100%)}
.caption{background:rgba(0,0,0,.88);color:var(--white);text-align:center;letter-spacing:.3px}
.cap1{left:266px;top:224px;width:304px;height:44px;font-size:24px;line-height:44px}
.cap2{left:298px;top:274px;width:236px;height:36px;font-size:19px;line-height:36px}
.arrow{top:237px}

.card{top:447px;width:219px;height:181px;background:var(--white);padding:6px}
.card-photo{height:104px}
.card h3{font-size:14px;font-weight:600;margin:14px 0 4px 2px}
.card p{font-size:8.3px;line-height:14px;color:var(--text);margin-left:2px}
.shadow{top:652px;width:200px;height:10px;border-radius:50%;background:radial-gradient(ellipse at center,rgba(0,0,0,.22),rgba(0,0,0,0) 70%)}
.rule{left:0;width:837px;height:1px;background:var(--line)}

/* products */
.section-title{font-size:14px;font-weight:600}
.product{top:722px;width:121px;height:152px;border:1px solid #ddd;background:var(--white);text-align:center}
.product-photo{width:90px;height:72px;margin:14px auto 0;border-radius:10px}
.product h4{font-size:12px;font-weight:400;color:#444;margin-top:14px}
.product p{font-size:8.3px;color:var(--muted);margin-top:3px}
.pshadow{top:872px;width:121px;height:10px;border-radius:50%;background:radial-gradient(ellipse at center,rgba(0,0,0,.2),rgba(0,0,0,0) 70%)}

/* welcome & news */
.intro{left:69px;top:977px;width:425px;font-size:8.3px;line-height:14.5px;color:var(--link)}
.body-copy{left:69px;top:1022px;width:425px;font-size:8.3px;line-height:14.5px;color:var(--text)}
.btn{left:69px;top:1097px;width:63px;height:24px;background:#1a1a1a;color:var(--white);font-size:7.5px;line-height:24px;text-align:center;letter-spacing:.3px}
.news{left:535px;width:240px}
.news a{display:block;font-size:9px;color:var(--link);text-decoration:none;margin-bottom:3px}
.news p{font-size:8.3px;line-height:14.5px;color:var(--text)}
.news time{font-size:8.3px;color:var(--muted)}

/* footer */
.footer{left:0;top:1140px;width:837px;height:60px;background:var(--footer)}
.copyright{left:70px;top:1163px;font-size:8.4px;color:#ddd}
</style>
</head>
<body>

<header>
  <div class="abs brand">
    <svg class="brand-mark" width="60" height="28" viewBox="0 0 60 28" aria-hidden="true"><rect x="3" y="2" width="18" height="18" fill="none" stroke="#1d1d1d" stroke-width="2"/></svg>
    <div class="brand-name">MAPLEWICK HAVEN SUPPLY</div>
    <div class="brand-tag">Packaging • Printing • Distribution</div>
  </div>
  <div class="abs call">
    <svg width="8" height="12" viewBox="0 0 8 12" aria-hidden="true"><rect x=".5" y=".5" width="7" height="11" rx="1.2" fill="none" stroke="#777"/><circle cx="4" cy="9.6" r=".8" fill="#777"/></svg>
    CALL US:<strong>000-000-000</strong>
  </div>
  <nav>
    <span class="abs nav active" style="left:317px">HOME</span>
    <span class="abs nav" style="left:386px">ABOUT US</span>
    <span class="abs nav" style="left:474px">SERVICES</span>
    <span class="abs nav" style="left:558px">PRODUCTS</span>
    <span class="abs nav" style="left:646px">NEWS</span>
    <span class="abs nav" style="left:711px">CONTACT US</span>
  </nav>
  <div class="abs nav-underline"></div>
</header>

<section class="abs band"></section>
<div class="abs slide"><div class="slide-photo" role="img" aria-label="Delivery courier carrying a cardboard box in front of a yellow van"></div></div>
<div class="abs caption cap1">MEETING ALL OF YOUR</div>
<div class="abs caption cap2">PACKAGING NEEDS</div>
<svg class="abs arrow" style="left:22px" width="26" height="58" viewBox="0 0 26 58" aria-hidden="true"><polyline points="25,1 1,29 25,57" fill="none" stroke="#fff" stroke-width="1.3"/></svg>
<svg class="abs arrow" style="left:796px" width="26" height="58" viewBox="0 0 26 58" aria-hidden="true"><polyline points="1,1 25,29 1,57" fill="none" stroke="#fff" stroke-width="1.3"/></svg>

<article class="abs card" style="left:69px">
  <div class="card-photo" role="img" aria-label="Worker with tablet among shipping boxes in a warehouse" style="background:radial-gradient(ellipse 30% 70% at 22% 45%,rgba(40,110,200,.85),rgba(40,110,200,0)),linear-gradient(180deg,#6e4a36 0%,#8d6446 55%,#c29468 100%)"></div>
  <h3>DISTRIBUTION</h3>
  <p>Lorem Ipsum is simply dummy text of the printing and typesetting industryorem Ipsum</p>
</article>
<article class="abs card" style="left:309px">
  <div class="card-photo" role="img" aria-label="Gloved hands at a printing press with colour proofs" style="background:radial-gradient(ellipse 35% 40% at 30% 60%,rgba(40,40,30,.85),rgba(40,40,30,0)),linear-gradient(180deg,#e6e6e4 0%,#d4d4d0 60%,#b9cf5a 85%,#6fa6c8 100%)"></div>
  <h3>PRINTING</h3>
  <p>Lorem Ipsum is simply dummy text of the printing and typesetting industryorem Ipsum</p>
</article>
<article class="abs card" style="left:548px">
  <div class="card-photo" role="img" aria-label="Hands lifting a cardboard box" style="background:radial-gradient(ellipse 45% 60% at 60% 50%,#caa073,rgba(202,160,115,0)),linear-gradient(90deg,#23382c 0%,#3e4f42 30%,#9b8066 70%,#7a6e66 100%)"></div>
  <h3>PACKAGING</h3>
  <p>Lorem Ipsum is simply dummy text of the printing and typesetting industryorem Ipsum</p>
</article>

<div class="abs shadow" style="left:78px"></div>
<div class="abs shadow" style="left:318px"></div>
<div class="abs shadow" style="left:557px"></div>
<div class="abs rule" style="top:669px"></div>

<h2 class="abs section-title" style="left:365px;top:693px">OUR PRODUCTS</h2>
<div class="abs product" style="left:70px"><div class="product-photo" role="img" aria-label="Stack of cardboard boxes" style="background:radial-gradient(ellipse 55% 50% at 50% 55%,#c99a4e,#e8cf9f 60%,#fff 100%)"></div><h4>Product Name</h4><p>Lorem Ipsum is simply</p></div>
<div class="abs product" style="left:218px"><div class="product-photo" role="img" aria-label="Coloured plastic storage bins" style="background:radial-gradient(ellipse 55% 50% at 50% 55%,#d8b83a,#c9574a 45%,#4d6ab8 70%,#fff 100%)"></div><h4>Product Name</h4><p>Lorem Ipsum is simply</p></div>
<div class="abs product" style="left:358px"><div class="product-photo" role="img" aria-label="Assorted light bulbs" style="background:radial-gradient(ellipse 55% 50% at 50% 50%,#b8bcc2,#dfe1e4 55%,#fff 100%)"></div><h4>Product Name</h4><p>Lorem Ipsum is simply</p></div>
<div class="abs product" style="left:498px"><div class="product-photo" role="img" aria-label="Calculator, pens and stapler" style="background:radial-gradient(ellipse 55% 50% at 50% 55%,#5a5a5a,#a49a92 55%,#fff 100%)"></div><h4>Product Name</h4><p>Lorem Ipsum is simply</p></div>
<div class="abs product" style="left:646px"><div class="product-photo" role="img" aria-label="Cleaning and janitorial supplies" style="background:radial-gradient(ellipse 55% 50% at 50% 55%,#5570b4,#c8584a 50%,#eef0f6 80%,#fff 100%)"></div><h4>Product Name</h4><p>Lorem Ipsum is simply</p></div>
<div class="abs pshadow" style="left:70px"></div>
<div class="abs pshadow" style="left:218px"></div>
<div class="abs pshadow" style="left:358px"></div>
<div class="abs pshadow" style="left:498px"></div>
<div class="abs pshadow" style="left:646px"></div>
<div class="abs rule" style="top:909px"></div>

<h2 class="abs section-title" style="left:69px;top:942px">WELCOME TO OUR SITE!!</h2>
<p class="abs intro">Lorem Ipsum is simply dummy text of the printing and typesetting industry. Lorem Ipsum has been the industry's standard dummy text ever since the 1500s, when an unknown printer.</p>
<p class="abs body-copy">Aook a galley of type and scrambled it to make a type specimen boolt has survived not only five centuries, but also the leap into electronic typesetting, remaining essentially unchanindustry's standard dummy text ever since the 1500s, when an unknown printeok a galley of type and scrambled it to make a type speci-men boolt has survived not only five centuries, but also the leap into electronic typesetti.</p>
<div class="abs btn">READ&nbsp; MORE</div>

<h2 class="abs section-title" style="left:535px;top:942px">NEWS</h2>
<div class="abs news" style="top:979px">
  <a href="#">Lorem Ipsum is simply dummy text</a>
  <p>typesetting industry. Lorem Ipsum has been the industry's standard dummy text ever since the 1500.</p>
  <time>April 10-2015</time>
</div>
<div class="abs news" style="top:1057px">
  <a href="#">Lorem Ipsum is simply dummy text</a>
  <p>typesetting industry. Lorem Ipsum has been the industry's standard dummy text ever since the 1500.</p>
  <time>April 10-2015</time>
</div>

<footer class="abs footer"></footer>
<p class="abs copyright">© Copyright&nbsp; maplewick haven Supply all rights are reserved</p>
<svg class="abs" style="left:642px;top:1156px" width="128" height="28" viewBox="0 0 128 28" role="img" aria-label="Contact and sharing links">
  <g fill="none" stroke="#fff" stroke-width="1.5">
    <circle cx="15" cy="14" r="12.5"/>
    <circle cx="49" cy="14" r="12.5"/>
    <circle cx="82" cy="14" r="12.5"/>
    <circle cx="113" cy="14" r="12.5"/>
  </g>
  <!-- envelope -->
  <g fill="none" stroke="#fff" stroke-width="1.3"><rect x="9" y="10" width="12" height="8"/><polyline points="9,10 15,15 21,10"/></g>
  <!-- phone -->
  <g fill="none" stroke="#fff" stroke-width="1.3"><rect x="45" y="7.5" width="8" height="13" rx="1.3"/></g>
  <circle cx="49" cy="18" r=".9" fill="#fff"/>
  <!-- pin -->
  <path d="M82 21 C78 16 77.5 14 77.5 12.5 A4.5 4.5 0 0 1 86.5 12.5 C86.5 14 86 16 82 21Z" fill="none" stroke="#fff" stroke-width="1.3"/>
  <circle cx="82" cy="12.5" r="1.4" fill="#fff"/>
  <!-- share arrow -->
  <g fill="none" stroke="#fff" stroke-width="1.3"><polyline points="108,19 108,13 118,13"/><polyline points="115,10 118,13 115,16"/></g>
</svg>

</body>
</html>
```